Brellwick Partners, LLC Stationary

Brellwick Partners, LLC is a new financial planning and consulting company. We are looking for designs on business cards, letterhead, envelopes, and anything else that would be useful. Our preference for business card design is two sided. We are looking for a professional and clean look with incorporating the logo and patriotic feel. Thank you to all who participate and good luck!

```html
<!DOCTYPE html>
<html lang="en">
<head>
<meta charset="utf-8">
<title>Brellwick Partners, LLC – Business Card</title>
<link href="https://fonts.googleapis.com/css2?family=Arimo:wght@400;700&display=swap" rel="stylesheet">
<style>
  :root {
    --page-bg: #e9e9ea;
    --navy: #1f3b6e;
    --red: #c0171f;
    --red-dark: #8a1016;
    --ink: #3d3d3d;
    --white: #ffffff;
  }
  * { box-sizing: border-box; margin: 0; padding: 0; }
  html, body { width: 1200px; height: 950px; overflow: hidden; }
  body {
    background: var(--page-bg);
    font-family: "Arimo", Arial, sans-serif;
    position: relative;
  }
  .card {
    position: absolute;
    left: 250px;
    width: 700px;
    height: 400px;
    box-shadow: 0 6px 18px rgba(0,0,0,0.18);
    overflow: hidden;
  }
  /* back side */
  .card-back {
    top: 50px;
    background: linear-gradient(115deg, var(--red) 0%, #b1141b 55%, var(--red-dark) 100%);
    display: flex;
    flex-direction: column;
    align-items: center;
    justify-content: center;
    gap: 26px;
  }
  .card-back .brand-name { color: var(--white); }
  .card-back .brand-mark { background: var(--white); }
  .card-back .website {
    color: rgba(255,255,255,0.8);
    font-size: 22px;
    letter-spacing: 3px;
  }
  /* front side */
  .card-front {
    top: 500px;
    background: var(--white);
  }
  .edge-band {
    position: absolute; left: 0; top: 0; bottom: 0;
    width: 18px; background: var(--navy);
  }
  .edge-line {
    position: absolute; left: 24px; top: 0; bottom: 0;
    width: 5px; background: var(--red);
  }
  .brand {
    display: flex; align-items: center; gap: 14px;
  }
  .card-front .brand {
    position: absolute; left: 66px; top: 46px;
  }
  .brand-mark {
    width: 34px; height: 34px; background: var(--navy);
  }
  .brand-name {
    font-size: 30px; font-weight: 700; color: var(--navy);
    letter-spacing: 1px;
  }
  .address {
    position: absolute; left: 66px; top: 132px;
    color: var(--ink); font-size: 21px; line-height: 28px;
  }
  .contact-list {
    position: absolute; left: 66px; top: 206px;
    list-style: none; color: var(--ink); font-size: 21px;
  }
  .contact-list li {
    display: flex; align-items: center; gap: 10px; height: 28px;
  }
  .contact-list svg { width: 17px; height: 17px; fill: var(--navy); flex: none; }
  .person {
    position: absolute; right: 110px; top: 286px; text-align: left;
  }
  .person-name { color: var(--navy); font-size: 26px; font-weight: 700; }
  .person-title { color: var(--red); font-size: 19px; margin-top: 4px; }
</style>
</head>
<body>

<section class="card card-back">
  <div class="brand">
    <span class="brand-mark"></span>
    <span class="brand-name">BRELLWICK PARTNERS, LLC</span>
  </div>
  <p class="website">www.brellwick.com</p>
</section>

<section class="card card-front">
  <div class="edge-band"></div>
  <div class="edge-line"></div>

  <div class="brand">
    <span class="brand-mark"></span>
    <span class="brand-name">BRELLWICK PARTNERS, LLC</span>
  </div>

  <address class="address" style="font-style:normal">
    4127 Larchmont Avenue<br>
    Cedar Hollow, NY 12045
  </address>

  <ul class="contact-list">
    <li>
      <svg viewBox="0 0 24 24" aria-hidden="true"><path d="M6.6 10.8a15.1 15.1 0 0 0 6.6 6.6l2.2-2.2a1 1 0 0 1 1-.25 11.4 11.4 0 0 0 3.6.57 1 1 0 0 1 1 1V20a1 1 0 0 1-1 1A17 17 0 0 1 3 4a1 1 0 0 1 1-1h3.5a1 1 0 0 1 1 1c0 1.25.2 2.45.57 3.57a1 1 0 0 1-.25 1z"/></svg>
      555 0147 2283
    </li>
    <li>
      <svg viewBox="0 0 24 24" aria-hidden="true"><path d="M6 3h12v5H6z M3 9h18v8h-3v4H6v-4H3z M8 15v4h8v-4z"/></svg>
      555 0193 4471
    </li>
    <li>
      <svg viewBox="0 0 24 24" aria-hidden="true"><path d="M2 5h20v14H2z M4 7v.5l8 5.5 8-5.5V7l-8 5.2z" fill-rule="evenodd"/></svg>
      dana@brellwick.com
    </li>
    <li>
      <svg viewBox="0 0 24 24" aria-hidden="true"><circle cx="12" cy="12" r="10"/><path d="M2 12h20M12 2c3 3 3 17 0 20M12 2c-3 3-3 17 0 20" stroke="#fff" stroke-width="1.5" fill="none"/></svg>
      www.brellwick.com
    </li>
  </ul>

  <div class="person">
    <p class="person-name">Dana Morrow</p>
    <p class="person-title">President</p>
  </div>
</section>

</body>
</html>
```